New Business Card Design Project

Use the flyer uploaded and website www.brightoakbuilders.com for inspiration.
List Our Services on Backside of business cards
Marcus Delling
Harborline Builders Inc.
Licensed General Contractors
858-471-6093

Contact Information for Business Card

Use the flyer uploaded and website www.brightoakbuilders.com for inspiration. List Our Services on Backside of business cards Marcus Delling Harborline Builders Inc. Licensed General Contractors 858-471-6093

```html
<!DOCTYPE html>
<html lang="en">
<head>
<meta charset="utf-8">
<title>Harborline Builders – Business Cards</title>
<link rel="stylesheet" href="https://fonts.googleapis.com/css2?family=Cinzel:wght@400;600&family=Montserrat:wght@400;500&display=swap">
<style>
  :root {
    --backdrop: #2b2b2d;
    --card: #161619;
    --ink: #f4f4f4;
    --accent: #e3212b;
  }
  * { box-sizing: border-box; margin: 0; padding: 0; }
  html, body { width: 1200px; height: 900px; overflow: hidden; }
  body {
    background: var(--backdrop);
    font-family: "Montserrat", Arial, sans-serif;
    color: var(--ink);
    position: relative;
  }
  .card {
    position: absolute;
    left: 250px;
    width: 700px;
    height: 400px;
    background: var(--card);
    border-bottom: 4px solid var(--accent);
    box-shadow: 0 10px 30px rgba(0,0,0,.5);
  }
  .card--services { top: 36px; }
  .card--contact { top: 464px; }

  .brand-name {
    font-family: "Montserrat", Arial, sans-serif;
    font-weight: 400;
    letter-spacing: 3px;
    text-transform: uppercase;
    color: var(--ink);
  }

  /* Services side */
  .card--services .brand-name {
    position: absolute;
    top: 140px; left: 0; right: 0;
    text-align: center;
    font-size: 30px;
  }
  .service-list {
    position: absolute;
    top: 270px; left: 0; right: 0;
    text-align: center;
    font-size: 17px;
    line-height: 1.55;
    letter-spacing: .3px;
  }
  .service-list .dot { color: var(--accent); margin: 0 6px; }

  /* Contact side */
  .card--contact .brand-name {
    position: absolute;
    top: 205px; left: 40px;
    width: 330px;
    text-align: center;
    font-size: 24px;
  }
  .divider {
    position: absolute;
    left: 392px; top: 110px;
    width: 1px; height: 170px;
    background: var(--accent);
  }
  .contact {
    position: absolute;
    left: 420px; top: 108px;
    width: 270px;
  }
  .contact__name {
    font-family: "Cinzel", Georgia, serif;
    font-weight: 600;
    font-size: 25px;
    color: var(--accent);
    letter-spacing: 1px;
    line-height: 1;
  }
  .contact__title { font-size: 14px; margin-top: 4px; }
  .contact__lines { list-style: none; margin-top: 20px; }
  .contact__lines li {
    display: flex; align-items: center; gap: 8px;
    font-size: 13.5px; line-height: 1.9;
  }
  .contact__lines svg { width: 13px; height: 13px; flex: none; }
  .contact__company { font-size: 14px; margin-top: 14px; }
</style>
</head>
<body>

<section class="card card--services">
  <div class="brand-name">Harborline Builders</div>
  <p class="service-list">
    Painting<span class="dot">•</span>Flooring<span class="dot">•</span>Kitchens<span class="dot">•</span>Custom Renovations<br>
    Bathrooms<span class="dot">•</span>Energy Efficienct Upgrades
  </p>
</section>

<section class="card card--contact">
  <div class="brand-name">Harborline Builders</div>
  <div class="divider"></div>
  <div class="contact">
    <div class="contact__name">Marcus Delling</div>
    <div class="contact__title">Licensed General Contractors</div>
    <ul class="contact__lines">
      <li>
        <svg viewBox="0 0 16 16" aria-hidden="true"><path fill="#e3212b" d="M3.5 1.5 6 4 4.8 5.7a9 9 0 0 0 5.5 5.5L12 10l2.5 2.5-1.6 2A11.5 11.5 0 0 1 1.5 3.1z"/></svg>
        858-471-6093
      </li>
      <li>
        <svg viewBox="0 0 16 16" aria-hidden="true"><rect x="1" y="3" width="14" height="10" fill="#e3212b"/><path d="M1 3l7 6 7-6" fill="none" stroke="#161619" stroke-width="1.4"/></svg>
        info@brightoakbuilders.com
      </li>
      <li>
        <svg viewBox="0 0 16 16" aria-hidden="true"><circle cx="8" cy="8" r="7" fill="#e3212b"/><path d="M1 8h14M8 1c-3 3.5-3 10.5 0 14M8 1c3 3.5 3 10.5 0 14" fill="none" stroke="#161619" stroke-width="1"/></svg>
        www.brightoakbuilders.com
      </li>
    </ul>
    <div class="contact__company">Harborline Builders Inc.</div>
  </div>
</section>

</body>
</html>
```